Professional & attention grabbing.

A business card design, front and back. I already have a logo I will attach, but I am open to something new as well.
Things to include:
Name:
Title:
Phone:
Email:
Wanting something that is professional but attention grabbing.
Also we do a lot of work using drones on natural gas pipelines (leading the future)if you want to include any of that. I'm open to ideas.
Target Market(s)
Natural gas transmission industry / greenhouse gas mitigation industry
Industry/Entity Type
Business
Colors
Designer to choose colors to be used in the design.
Look and feel
Each slider illustrates characteristics of the customer's brand and the style your logo design should communicate.

```html
<!DOCTYPE html>
<html lang="en">
<head>
<meta charset="utf-8">
<title>KV Field Inspections – Business Card</title>
<link rel="stylesheet" href="https://fonts.googleapis.com/css2?family=Michroma&family=Roboto:wght@400;500&family=Roboto+Condensed:wght@600&display=swap">
<style>
  :root {
    --backdrop: #e4dfd8;
    --card: #3b3b3d;
    --card-edge: #4a4a4c;
    --accent: #c8322b;
    --divider: #c9b9a4;
    --text-main: #ececec;
    --text-muted: #c4c4c4;
  }
  * { margin: 0; padding: 0; box-sizing: border-box; }
  html, body {
    width: 1200px; height: 1010px; overflow: hidden;
    background: var(--backdrop);
  }
  .business-card {
    position: absolute;
    left: 172px; top: 258px;
    width: 856px; height: 494px;
    background: var(--card);
    border: 1px solid var(--card-edge);
    border-radius: 3px;
    box-shadow: 0 10px 30px rgba(0,0,0,0.18);
  }
  .brand {
    position: absolute;
    left: 66px; top: 196px;
    display: flex; align-items: center; gap: 16px;
  }
  .brand-square {
    width: 58px; height: 58px;
    background: var(--accent);
  }
  .brand-name {
    font-family: "Roboto Condensed", sans-serif;
    font-weight: 600;
    font-size: 25px;
    letter-spacing: 0.5px;
    color: #ffffff;
  }
  .divider {
    position: absolute;
    left: 411px; top: 135px;
    width: 2px; height: 221px;
    background: var(--divider);
  }
  .contact-block {
    position: absolute;
    left: 447px; top: 166px;
  }
  .person-name {
    font-family: "Michroma", sans-serif;
    font-size: 21px;
    color: var(--accent);
    letter-spacing: 1px;
    line-height: 30px;
  }
  .person-title {
    font-family: "Roboto", sans-serif;
    font-size: 17px;
    color: var(--text-muted);
    margin-top: 3px;
  }
  .contact-list {
    list-style: none;
    margin-top: 22px;
  }
  .contact-item {
    display: flex; align-items: center; gap: 14px;
    font-family: "Roboto", sans-serif;
    font-size: 18.5px;
    color: var(--text-main);
    height: 28px;
  }
  .contact-icon { width: 18px; height: 18px; flex: none; fill: var(--accent); }
</style>
</head>
<body>
  <main class="business-card">
    <div class="brand">
      <div class="brand-square"></div>
      <span class="brand-name">KV Field Inspections</span>
    </div>

    <div class="divider"></div>

    <section class="contact-block">
      <h1 class="person-name">DANIEL REYES</h1>
      <p class="person-title">Managing Director</p>
      <ul class="contact-list">
        <li class="contact-item">
          <svg class="contact-icon" viewBox="0 0 24 24" aria-hidden="true">
            <path d="M3 9c0-3 4-5 9-5s9 2 9 5v2h-5V9c-1-1-7-1-8 0v2H3z"/>
            <path d="M6 12h12l2 8H4z"/>
          </svg>
          1300 484 484
        </li>
        <li class="contact-item">
          <svg class="contact-icon" viewBox="0 0 24 24" aria-hidden="true">
            <path d="M12 2a10 10 0 1 0 0 20 10 10 0 0 0 0-20zm6.9 6h-3a15 15 0 0 0-1.3-4A8 8 0 0 1 18.9 8zM12 4c.8 1.1 1.5 2.5 1.9 4h-3.8c.4-1.5 1.1-2.9 1.9-4zM4.3 14a8 8 0 0 1 0-4h3.4a16 16 0 0 0 0 4zm.8 2h3a15 15 0 0 0 1.3 4A8 8 0 0 1 5.1 16zm3-8h-3a8 8 0 0 1 4.3-4 15 15 0 0 0-1.3 4zM12 20c-.8-1.1-1.5-2.5-1.9-4h3.8c-.4 1.5-1.1 2.9-1.9 4zm2.3-6H9.7a14 14 0 0 1 0-4h4.6a14 14 0 0 1 0 4zm.3 6a15 15 0 0 0 1.3-4h3a8 8 0 0 1-4.3 4zm1.7-6a16 16 0 0 0 0-4h3.4a8 8 0 0 1 0 4z"/>
          </svg>
          www.kvfieldinspect.com
        </li>
        <li class="contact-item">
          <svg class="contact-icon" viewBox="0 0 24 24" aria-hidden="true">
            <path d="M2 5h20v14H2z" />
            <path d="M2 5l10 8 10-8" fill="none" stroke="#3b3b3d" stroke-width="2"/>
          </svg>
          daniel.reyes@kvfieldinspect.com
        </li>
      </ul>
    </section>
  </main>
</body>
</html>
```